Kitchen and custom cabinetry company looking for business card design

We make: * Custom Kitchens, contemporary and traditional kitchens, Vanities, Libraries, Custom Entry Doors, Custom Wine Cellars and Custom Design Furniture. Phone number 555-284-7716. Address: Westhampton NY. Email: KAVRO@mailbox.example Portfolio at: KAVROcabinetry.example I would like moderns fonts and not heavy lines. double side but maybe will use clear plastic. I attached the logo.

Industry/Entity Type

Business

```html
<!DOCTYPE html>
<html lang="en">
<head>
<meta charset="utf-8">
<title>Kavro Cabinetry Inc. – Business Card</title>
<link rel="stylesheet" href="https://fonts.googleapis.com/css2?family=Bitter:wght@400;700&family=Alegreya+Sans:wght@400;500&display=swap">
<style>
  :root {
    --bg: #e8e5e1;
    --orange: #f15a29;
    --orange-soft: #f58660;
    --grey: #808080;
    --grey-soft: #b8b8b8;
    --white: #ffffff;
    --name-grey: #7f7f7f;
  }
  * { margin: 0; padding: 0; box-sizing: border-box; }
  html, body {
    width: 1200px; height: 970px; overflow: hidden;
    background: var(--bg);
  }
  .canvas { position: relative; width: 1200px; height: 970px; }

  .card {
    position: absolute; top: 126px; width: 409px; height: 715px;
    border-radius: 20px; overflow: hidden;
  }
  .card--front { left: 149px; --accent: var(--orange); --accent-soft: var(--orange-soft); }
  .card--back  { left: 654px; --accent: var(--grey);   --accent-soft: var(--grey-soft); }

  .card__cap   { position: absolute; top: 0; left: 0; right: 0; height: 30px; background: var(--accent); }
  .card__brand {
    position: absolute; top: 30px; left: 0; right: 0; height: 268px;
    background: var(--white);
    display: flex; align-items: center; justify-content: center;
  }
  .card__stripe { position: absolute; top: 324px; left: 0; right: 0; height: 47px; background: var(--accent-soft); }
  .card__panel {
    position: absolute; top: 395px; left: 0; right: 0; bottom: 0;
    background: var(--accent); color: var(--white);
    text-align: center;
  }

  .brand__name {
    font-family: "Alegreya Sans", sans-serif; font-weight: 500;
    color: var(--name-grey); font-size: 30px; letter-spacing: 3px;
    line-height: 1; text-align: center;
  }

  .contact { padding-top: 55px; font-family: "Alegreya Sans", sans-serif; font-size: 17.5px; line-height: 20.5px; }
  .contact__name { font-family: "Bitter", serif; font-weight: 700; font-size: 20px; line-height: 22px; }
  .contact__role { font-size: 16px; line-height: 20px; margin-bottom: 24px; }
  .contact__address { margin-bottom: 36px; }

  .specialties { padding-top: 78px; }
  .specialties__title {
    font-family: "Bitter", serif; font-weight: 700; font-size: 20px;
    letter-spacing: 0.8px; margin-bottom: 20px;
  }
  .specialties__list {
    list-style: none; font-family: "Bitter", serif; font-weight: 400;
    font-size: 15px; line-height: 20.5px; letter-spacing: 0.8px;
  }
</style>
</head>
<body>
<main class="canvas">

  <section class="card card--front" aria-label="Card front">
    <div class="card__cap"></div>
    <div class="card__brand">
      <p class="brand__name">KAVRO CABINETRY INC.</p>
    </div>
    <div class="card__stripe"></div>
    <div class="card__panel contact">
      <p class="contact__name">Marco Delgado</p>
      <p class="contact__role">Owner</p>
      <p class="contact__address">220 Harbor Point rd,<br>Eastport, NY, 11940</p>
      <p>555-284-7716<br>kavro@mailbox.example<br>www.kavrocabinetry.example</p>
    </div>
  </section>

  <section class="card card--back" aria-label="Card back">
    <div class="card__cap"></div>
    <div class="card__brand">
      <p class="brand__name">KAVRO CABINETRY INC.</p>
    </div>
    <div class="card__stripe"></div>
    <div class="card__panel specialties">
      <h2 class="specialties__title">OUR SPECIALTIES</h2>
      <ul class="specialties__list">
        <li>CONTEMPORARY KITCHENS</li>
        <li>TRADITIONAL KITCHENS</li>
        <li>VANITIES</li>
        <li>LIBRARIES</li>
        <li>CUSTOM WINE CELLARS</li>
        <li>CUSTOM DESIGN FURNITURE</li>
      </ul>
    </div>
  </section>

</main>
</body>
</html>
```